Vantoq Business Card Project showing the logo and a marbo image on the rear

Design a whacky but professional business card, the logo is for the front and the Marbo image is for the rear. Happy to consider other open source Marbo Images if the designer wants to select one from the web. Vantoq is a competitor to OMB.com.au and Pellory.com.au and is based around every property in Australia

Target Market(s)

Business

Contact Information for Business Card

Name, Title, Email, Web, Phone Number

Font styles to use
Other font styles liked:
• avenir

Requirements
Must have
• Image on Back logo on front
Nice to have
• Happy to consider other images on rear, preftably Colin Marbo. Image supplied I own, we can use open source other Marbo Images

```html
<!DOCTYPE html>
<html lang="en">
<head>
<meta charset="utf-8">
<title>Vantoq Business Card</title>
<link rel="stylesheet" href="https://fonts.googleapis.com/css2?family=Jost:wght@600&family=Roboto:wght@400&family=Outfit:wght@500&display=swap">
<style>
  :root {
    --page-bg: #262626;
    --card-white: #f4f4f4;
    --brand-orange: #e8870f;
    --ink: #141414;
    --night: #3a3b3d;
    --art-green: #8cc63f;
    --art-blue: #4bb4d6;
  }
  * { margin: 0; padding: 0; box-sizing: border-box; }
  html, body {
    width: 1200px; height: 1138px; overflow: hidden;
    background: var(--page-bg);
  }
  .card {
    position: absolute; left: 290px;
    width: 620px; height: 376px;
    border-radius: 16px; overflow: hidden;
  }
  .card-back { top: 184px; }
  .card-front { top: 606px; background: var(--card-white); }

  .artwork {
    width: 100%; height: 100%;
    background:
      linear-gradient(180deg, rgba(0,0,0,0) 0%, rgba(0,0,0,0) 55%, rgba(232,80,140,0.55) 75%, var(--art-blue) 92%, var(--art-green) 100%),
      linear-gradient(90deg, var(--brand-orange) 0%, var(--brand-orange) 46%, var(--night) 52%, var(--night) 100%);
  }

  .wave { position: absolute; left: 0; top: 0; }

  .brand {
    position: absolute; left: 66px; top: 196px;
    display: flex; align-items: center; gap: 14px;
  }
  .brand-mark { width: 34px; height: 34px; background: var(--brand-orange); }
  .brand-name {
    font-family: "Jost", sans-serif; font-weight: 600;
    font-size: 62px; line-height: 1; color: var(--ink);
  }

  .identity { position: absolute; right: 30px; top: 50px; text-align: right; }
  .person-name {
    font-family: "Outfit", sans-serif; font-weight: 500;
    font-size: 25px; color: var(--brand-orange); line-height: 1.1;
  }
  .person-title, .address {
    font-family: "Roboto", sans-serif; font-size: 16px; color: var(--ink); line-height: 1.25;
  }
  .person-title { margin-top: 4px; }
  .address { position: absolute; right: 30px; top: 138px; text-align: right; }

  .contact {
    position: absolute; right: 30px; top: 276px;
    list-style: none; font-family: "Roboto", sans-serif; font-size: 16px; color: var(--ink);
  }
  .contact li {
    display: flex; justify-content: flex-end; align-items: center;
    gap: 14px; height: 24px;
  }
  .contact svg { width: 14px; height: 14px; }
</style>
</head>
<body>
  <section class="card card-back">
    <div class="artwork" role="img" aria-label="Colourful hand-drawn city of cheerful buildings with a train below, day sky on the left and night sky on the right"></div>
  </section>

  <section class="card card-front">
    <svg class="wave" width="620" height="376" viewBox="0 0 620 376" aria-hidden="true">
      <path d="M0,376 L0,306 C130,334 220,330 340,286 C440,250 530,236 620,244 L620,376 Z" fill="var(--brand-orange)"/>
      <path d="M0,296 C130,326 220,322 336,276 C440,234 530,220 620,228" fill="none" stroke="var(--ink)" stroke-width="7"/>
      <path d="M48,286 C140,300 230,296 310,270" fill="none" stroke="var(--ink)" stroke-width="2"/>
    </svg>

    <div class="brand">
      <span class="brand-mark"></span>
      <span class="brand-name">Vantoq</span>
    </div>

    <div class="identity">
      <p class="person-name">Noel Bramwell</p>
      <p class="person-title">Founder &amp; CEO</p>
    </div>

    <p class="address">Level 4, 18 Carrow Lane,<br>Sydney 2000, Australia</p>

    <ul class="contact">
      <li>(00) 5555 0148
        <svg viewBox="0 0 14 14" aria-hidden="true"><circle cx="7" cy="7" r="6" fill="none" stroke="var(--ink)" stroke-width="1.3"/><path d="M4.6,4 L5.8,4 L6.3,5.6 L5.6,6.2 C6,7.2 6.8,8 7.8,8.4 L8.4,7.7 L10,8.2 L10,9.4 C7,9.6 4.4,7 4.6,4 Z" fill="var(--ink)"/></svg>
      </li>
      <li>bramwell@vantoq.com
        <svg viewBox="0 0 14 14" aria-hidden="true"><rect x="1" y="3" width="12" height="8" fill="var(--ink)"/><path d="M1,3 L7,8 L13,3" fill="none" stroke="var(--brand-orange)" stroke-width="1.2"/></svg>
      </li>
      <li>www.vantoq.com
        <svg viewBox="0 0 14 14" aria-hidden="true"><circle cx="7" cy="7" r="6" fill="var(--ink)"/><path d="M1,7 H13 M7,1 V13 M7,1 C4,4 4,10 7,13 M7,1 C10,4 10,10 7,13" fill="none" stroke="var(--brand-orange)" stroke-width="0.8"/></svg>
      </li>
    </ul>
  </section>
</body>
</html>
```